colour pencil case design

I am looking for a design for the front of a pencil case. The pencil case has 2 versions, 1 white fabric and 1 black fabric. The design should have 2 versions, eg. white word on black fabric and black words on white fabric. Its for children and teenagers’ aged 7 to 18. I can have 2 separate designs.
The pencil case is 22cm by 14cm. So the size of the image should be 18cm by 11cm. Files should be in png format and already in the correct size.
It must have the word “Believe”in big size. The letter b can be in capps or small letter. Prefer the font used in
I am looking for a background or image that can represent the phrase. If the design is good, I am open to also black and white theme.
Can also be black and white or colour... I have attached the font that I like for the main word "Believe". https://www.quillnest.net/gallery/583047192/Free-Font-Corvena-Modern-Script. Or you can use this font for the word Believe as well…. "Playlist script
Besides the word Believe, you should have the sentence ‘you can and you will”. It can be all in capps or small letter. (smaller size and different font from your word.
Target Market(s)
children and teenagers
Industry/Entity Type
tuition
Requirements
Must have
- The word Believe and the phrase I can and I will
Nice to have
- Some colourful pictures that can represent the phrase

```html
<!DOCTYPE html>
<html lang="en">
<head>
<meta charset="utf-8">
<title>Believe – Pencil Case Front, Light and Dark Versions</title>
<link rel="stylesheet" href="https://fonts.googleapis.com/css2?family=Yellowtail&family=Poiret+One&display=swap">
<style>
  :root {
    --canvas: #ffffff;
    --fabric-light: #f3f3f3;
    --fabric-dark: #151515;
    --ink-dark: #0a0a0a;
    --ink-light: #ffffff;
    --rule-light: #b8b8b8;
    --rule-dark: #9a9a9a;
    --ring-light: #c4c4c4;
    --ring-dark: #bdbdbd;
  }
  * { margin: 0; padding: 0; box-sizing: border-box; }
  html, body {
    width: 997px;
    height: 1200px;
    overflow: hidden;
    background: var(--canvas);
  }
  .sheet {
    position: relative;
    width: 997px;
    height: 1200px;
  }
  .case-front {
    position: absolute;
    left: 72px;
    width: 852px;
    height: 518px;
    overflow: hidden;
  }
  .case-front--white {
    top: 48px;
    background: linear-gradient(180deg, #f8f8f8 0%, var(--fabric-light) 60%, #ececec 100%);
  }
  .case-front--black {
    top: 621px;
    background: linear-gradient(180deg, #1b1b1b 0%, var(--fabric-dark) 60%, #101010 100%);
  }
  .case-art {
    display: block;
    width: 852px;
    height: 518px;
  }
  .headline {
    font-family: "Yellowtail", cursive;
    font-size: 300px;
  }
  .tagline {
    font-family: "Poiret One", sans-serif;
    font-size: 18px;
    font-weight: 700;
    letter-spacing: 1.2px;
  }
  .case-front--white .headline,
  .case-front--white .tagline { fill: var(--ink-dark); }
  .case-front--black .headline,
  .case-front--black .tagline { fill: var(--ink-light); }
  .case-front--white .rule { stroke: var(--rule-light); }
  .case-front--black .rule { stroke: var(--rule-dark); }
  .case-front--white .ring { stroke: var(--ring-light); }
  .case-front--black .ring { stroke: var(--ring-dark); }
  .ring { fill: none; stroke-width: 5; }
</style>
</head>
<body>
<main class="sheet">

  <section class="case-front case-front--white" aria-label="Light fabric version">
    <svg class="case-art" viewBox="0 0 852 518" xmlns="http://www.w3.org/2000/svg">
      <text class="headline" x="84" y="262" textLength="684" lengthAdjust="spacingAndGlyphs">Believe</text>
      <text class="tagline" x="516" y="330" textLength="244" lengthAdjust="spacingAndGlyphs">YOU CAN AND YOU WILL</text>
      <line class="rule" x1="84" y1="351" x2="790" y2="351" stroke-width="1"/>
      <line class="rule" x1="150" y1="356" x2="760" y2="356" stroke-width="0.8"/>
      <ellipse class="ring" cx="60" cy="560" rx="72" ry="62"/>
      <ellipse class="ring" cx="234" cy="566" rx="104" ry="104"/>
      <ellipse class="ring" cx="800" cy="560" rx="64" ry="66"/>
    </svg>
  </section>

  <section class="case-front case-front--black" aria-label="Dark fabric version">
    <svg class="case-art" viewBox="0 0 852 518" xmlns="http://www.w3.org/2000/svg">
      <text class="headline" x="84" y="262" textLength="684" lengthAdjust="spacingAndGlyphs">Believe</text>
      <text class="tagline" x="516" y="330" textLength="244" lengthAdjust="spacingAndGlyphs">YOU CAN AND YOU WILL</text>
      <line class="rule" x1="78" y1="351" x2="790" y2="351" stroke-width="1.2"/>
      <line class="rule" x1="150" y1="357" x2="760" y2="357" stroke-width="0.8"/>
      <ellipse class="ring" cx="60" cy="560" rx="72" ry="62"/>
      <ellipse class="ring" cx="234" cy="566" rx="104" ry="104"/>
      <ellipse class="ring" cx="800" cy="560" rx="64" ry="66"/>
    </svg>
  </section>

</main>
</body>
</html>
```